Corvel Creamery Works ( Australian Dairy site )

We need a new website we are a new company in Australia manufacturing dairy products ( Packing Butter ) We want to have a new modern punchy website with the basic details of the company and company certifications should be linked in a pdf etc.. maybe photos of the site modernised graphics etc.. we need to show our customers our brand clean and green image of Australian high quality products packed under strict Australian quality standards.

Target Market(s)

export - Asia

Industry/Entity Type

It Company

Number of Pages Required

5+ page

Requirements
Must have
• Home page
• About us page
• Products page
• Contact us page
• Facility / Accreditations ( Under facility pdf files eg Licenses, halal etc.. )

```html
<!DOCTYPE html>
<html lang="en">
<head>
<meta charset="utf-8">
<title>Our Facility – Corvel Creamery Works</title>
<link href="https://fonts.googleapis.com/css2?family=Varela+Round&family=Satisfy&display=swap" rel="stylesheet">
<style>
:root{
  --sky:#5fa9ef;
  --sky-light:#a9d3fb;
  --leaf:#2f9a3a;
  --leaf-dark:#27862f;
  --gold:#f4b020;
  --bark:#5e4a3b;
  --bark-dark:#4c3b2e;
  --white:#ffffff;
  --cream:#efe6dc;
  --ink-soft:#d9cfc5;
}
*{margin:0;padding:0;box-sizing:border-box}
html,body{width:716px;height:1200px;overflow:hidden}
body{position:relative;font-family:"Varela Round",sans-serif;color:var(--white);background:var(--white)}
.backdrop{position:absolute;left:0;top:0}
.abs{position:absolute}
.brand{left:80px;top:20px;display:flex;align-items:center;gap:8px}
.brand-dot{width:44px;height:44px;border-radius:50%;background:var(--leaf)}
.brand-name{font-size:13px;line-height:14px;color:var(--leaf-dark);width:110px}
.nav{top:39px;left:300px;display:flex;gap:0;font-size:6.6px;letter-spacing:.2px}
.nav a{color:var(--white);text-decoration:none;position:absolute;white-space:nowrap}
.nav a.current{color:var(--leaf-dark)}
.page-title{top:88px;left:0;width:716px;text-align:center;font-family:"Satisfy",cursive;font-size:40px;text-shadow:0 2px 3px rgba(0,0,0,.15)}
.intro{top:151px;left:76px;width:564px;text-align:center;font-size:6.4px;line-height:11.3px}
.lead{top:205px;left:78px;font-size:8.6px}
.equipment{top:230px;left:78px;list-style:none;font-size:14px;line-height:17.2px}
.equipment li::before{content:"•";margin-right:8px}
.section-title{top:410px;left:0;width:716px;text-align:center;font-family:"Satisfy",cursive;font-size:27px}
.slide{top:486px;left:128px;width:461px;height:291px;background:var(--white);padding:5px;box-shadow:0 2px 8px rgba(0,0,0,.25)}
.slide-photo{width:100%;height:100%;background:linear-gradient(180deg,#c9d1d6 0%,#9ea8ae 55%,#1f4f9a 80%,#17428a 100%)}
.arrow{width:34px;height:34px;border-radius:50%;background:var(--white);top:614px;display:flex;align-items:center;justify-content:center}
.arrow.prev{left:79px}.arrow.next{left:602px}
.thumbs{top:885px;left:0}
.thumb{position:absolute;top:0;width:93px;height:63px;background:var(--white);padding:3px;box-shadow:0 1px 4px rgba(0,0,0,.3)}
.thumb div{width:100%;height:100%;background:linear-gradient(180deg,#b9c2c8,#6f7f8c 70%,#2b5a9c)}
.foot-title{top:1037px;font-size:14px;color:var(--white)}
.foot-list{list-style:none;font-size:6.4px;line-height:11.5px;color:var(--cream)}
.contact-line{font-size:6.4px;color:var(--cream);display:flex;gap:5px;align-items:flex-start}
.newsletter-note{top:1066px;left:338px;font-size:6px;color:var(--ink-soft)}
.email-field{top:1086px;left:337px;width:117px;height:21px;background:var(--bark-dark);font-size:6px;color:var(--cream);padding:7px 6px}
.subscribe{top:1118px;left:338px;width:50px;height:15px;background:var(--leaf);font-size:6px;text-align:center;line-height:15px}
.footer-brand{top:1043px;left:480px;display:flex;align-items:center;gap:8px}
.footer-brand .brand-dot{width:50px;height:50px;background:#8f8a85}
.footer-brand .brand-name{color:#a6a09a;font-size:12px;width:100px}
.social{top:1097px;width:24px;height:24px;border-radius:50%;background:var(--leaf)}
.copyright{top:1167px;left:0;width:716px;text-align:center;font-size:6.4px;color:var(--cream)}
</style>
</head>
<body>
<svg class="backdrop" width="716" height="1200" viewBox="0 0 716 1200" aria-hidden="true">
  <defs>
    <linearGradient id="sky" x1="0" y1="0" x2="0" y2="1">
      <stop offset="0" stop-color="#58a3ec"/><stop offset="1" stop-color="#64adf1"/>
    </linearGradient>
    <radialGradient id="glow" cx="160" cy="35" r="120" gradientUnits="userSpaceOnUse">
      <stop offset="0" stop-color="#ffffff" stop-opacity=".95"/><stop offset="1" stop-color="#ffffff" stop-opacity="0"/>
    </radialGradient>
    <radialGradient id="leaf" cx="358" cy="600" r="380" gradientUnits="userSpaceOnUse">
      <stop offset="0" stop-color="#35a53f"/><stop offset="1" stop-color="#2a8f33"/>
    </radialGradient>
  </defs>
  <rect x="0" y="0" width="716" height="400" fill="url(#sky)"/>
  <rect x="0" y="0" width="716" height="200" fill="url(#glow)"/>
  <path d="M0,342 Q358,372 716,338 L716,1200 L0,1200Z" fill="#fff"/>
  <path d="M20,347 Q358,392 716,342 L716,350 Q358,400 0,352Z" fill="var(--gold)"/>
  <path d="M0,352 Q358,400 716,350 L716,804 Q358,868 0,804Z" fill="url(#leaf)"/>
  <path d="M0,958 Q358,1008 716,952 L716,1200 L0,1200Z" fill="var(--bark)"/>
  <path d="M95,975 Q358,995 622,970 Q358,1010 95,975Z" fill="var(--gold)"/>
</svg>

<div class="abs brand"><span class="brand-dot"></span><span class="brand-name">Corvel Creamery Works</span></div>
<nav class="abs nav">
  <a href="#" style="left:0">HOME</a>
  <a href="#" style="left:45px">ABOUT US</a>
  <a href="#" style="left:102px">PRODUCTS</a>
  <a href="#" class="current" style="left:161px">FACILITY</a>
  <a href="#" style="left:213px">ACCREDITATIONS</a>
  <a href="#" style="left:293px">CONTACT US</a>
</nav>

<h1 class="abs page-title">Our Facility</h1>
<p class="abs intro">Corvel Creamery Works has a state of the art, fully accredited production facility in Kellbrook North, Victoria. We have the latest process and technology enabling us to produce the highest quality butter pats in different pack formats. CCW quality management system ensures that our products are compliant to the most stringent domestic and International regulatory requirements to deliver the highest quality product.</p>
<p class="abs lead">Our facility has the following equipment and technology</p>
<ul class="abs equipment">
  <li>Velmont Butter Wrapping machines</li>
  <li>Foreign matter inspection by X-ray machines - for quality control</li>
  <li>Positive Air pressure – to maintain an hygienic clean environment</li>
  <li>Online check weigher</li>
  <li>Automatic case packers</li>
  <li>hygienic entrance systems</li>
</ul>

<h2 class="abs section-title">Foreign matter inspection by X-ray machines</h2>
<div class="abs slide"><div class="slide-photo" role="img" aria-label="X-ray inspection machine on the butter packing line"></div></div>
<a href="#" class="abs arrow prev" aria-label="Previous"><svg width="12" height="12" viewBox="0 0 12 12"><path d="M8 2 L4 6 L8 10" fill="none" stroke="#555" stroke-width="2.2"/></svg></a>
<a href="#" class="abs arrow next" aria-label="Next"><svg width="12" height="12" viewBox="0 0 12 12"><path d="M4 2 L8 6 L4 10" fill="none" stroke="#555" stroke-width="2.2"/></svg></a>

<div class="abs thumbs">
  <div class="thumb" style="left:80px"><div role="img" aria-label="Hygienic entrance turnstile"></div></div>
  <div class="thumb" style="left:194px"><div role="img" aria-label="X-ray inspection machine"></div></div>
  <div class="thumb" style="left:313px"><div role="img" aria-label="Butter wrapping machine close-up"></div></div>
  <div class="thumb" style="left:428px"><div role="img" aria-label="Packing line conveyors"></div></div>
  <div class="thumb" style="left:546px"><div role="img" aria-label="Automatic case packer"></div></div>
</div>

<h3 class="abs foot-title" style="left:77px">Quick Links</h3>
<ul class="abs foot-list" style="top:1062px;left:77px">
  <li>Home</li><li>About us</li><li>Products</li><li>Facility</li><li>Accreditations</li><li>Contact us</li>
</ul>

<h3 class="abs foot-title" style="left:196px">Contact Us</h3>
<div class="abs contact-line" style="top:1065px;left:196px"><svg width="7" height="7" viewBox="0 0 10 10"><path d="M2 1 L4 1 L5 3.5 L3.8 4.5 Q5 6.5 6 6.2 L7 5 L9.5 6 L9.5 8 Q5 10 1 3Z" fill="var(--cream)"/></svg><span>+61 3 9000 4182</span></div>
<div class="abs contact-line" style="top:1077px;left:196px"><svg width="7" height="7" viewBox="0 0 10 10"><rect x="1" y="2" width="8" height="6" fill="none" stroke="var(--cream)"/><path d="M1 2 L5 5.5 L9 2" fill="none" stroke="var(--cream)"/></svg><span>info@corvelcreamery.com.au</span></div>
<div class="abs contact-line" style="top:1099px;left:196px;line-height:11.5px"><svg width="7" height="8" viewBox="0 0 10 12"><path d="M5 11 Q1 6 1 4 A4 4 0 0 1 9 4 Q9 6 5 11Z" fill="var(--cream)"/></svg><span>12 Farrow Lane, Kellbrook North,<br>Victoria 3099 Australia</span></div>

<h3 class="abs foot-title" style="left:339px">Newsletter</h3>
<p class="abs newsletter-note">Sign Up for Our Newsletter &amp; Promotion</p>
<div class="abs email-field">Enter Your email Id</div>
<div class="abs subscribe">SUBSCRIBE</div>

<div class="abs footer-brand"><span class="brand-dot"></span><span class="brand-name">Corvel Creamery Works</span></div>
<a href="#" class="abs social" style="left:557px" aria-label="Social profile"></a>
<a href="#" class="abs social" style="left:584px" aria-label="Social profile"></a>
<a href="#" class="abs social" style="left:613px" aria-label="Social profile"></a>

<p class="abs copyright">© 2016 corvelcreamery.com.au</p>
</body>
</html>
```